Vacation Rental Postcard Design

The Kingfisher's Perch is a vacation rental cottage. We want a postcard that can be used as promotional give-aways for visitors as well as something that can be given to the tourism board and local merchants to help us promote the rental.

Our tag line is" The Kingfisher's Perch - the finest perch on the ridge!". Should also include "Cedarholm, WA USA"

We have also used "Come see what all of the buzz is about"

Want to include our info in small print on the mailing side portion of the postcard:

KLWT: www.klwtstays.example/417294
Chatterly: www.chatterly.example/thefinestperchontheridge

Target Market(s)

Couples, romantic, honeymooners, coming for wine tasting, hot air ballooning, hiking, enjoying nature

Industry/Entity Type

Tourism

```html
<!DOCTYPE html>
<html lang="en">
<head>
<meta charset="utf-8">
<title>The Kingfisher's Perch – Postcard</title>
<link rel="stylesheet" href="https://fonts.googleapis.com/css2?family=Jost:ital,wght@0,300;0,400;0,500;1,300&display=swap">
<style>
  :root {
    --page: #f1f1f1;
    --card: #ffffff;
    --ink: #111111;
    --rule: #2a2a2a;
    --faint: #e9e9e9;
    --faint-ink: #cfcfcf;
  }
  * { box-sizing: border-box; margin: 0; padding: 0; }
  html, body { width: 763px; height: 1200px; overflow: hidden; }
  body { background: var(--page); font-family: "Jost", "Futura", sans-serif; color: var(--ink); position: relative; }

  .postcard {
    position: absolute; left: 31px; width: 701px; height: 544px;
    background: var(--card);
    box-shadow: 0 2px 8px rgba(0,0,0,0.12);
    overflow: hidden;
  }
  .postcard--mailing { top: 33px; }
  .postcard--photo { top: 614px; }

  /* Mailing side */
  .brand-backdrop { position: absolute; left: 205px; top: 95px; width: 340px; height: 340px; }
  .brand-backdrop__circle { position: absolute; inset: 0; border-radius: 50%; background: var(--faint); opacity: 0.7; }
  .brand-backdrop__name {
    position: absolute; left: 172px; width: 160px; top: 40px; text-align: center;
    font-size: 21px; font-weight: 400; line-height: 1.15; color: var(--faint-ink);
  }
  .headline {
    position: absolute; left: 44px; top: 50px;
    font-size: 27px; font-weight: 500; line-height: 1.08; letter-spacing: -0.2px;
  }
  .stamp-box { position: absolute; left: 556px; top: 44px; width: 96px; height: 121px; border: 1.5px solid var(--rule); }
  .rule { position: absolute; height: 0; border-top: 1.2px solid var(--rule); }
  .rule--greeting { left: 44px; top: 177px; width: 170px; }
  .message-lines .rule { left: 44px; width: 321px; }
  .address-lines .rule { left: 457px; width: 199px; }
  .contact {
    position: absolute; top: 491px; font-size: 12.5px; font-weight: 400; color: #333; letter-spacing: -0.1px;
  }
  .contact--listing { left: 38px; }
  .contact--social { right: 26px; }
  .brand-mini {
    position: absolute; left: 218px; top: 485px; width: 100px; height: 26px;
    display: flex; align-items: center; gap: 4px;
  }
  .brand-mini__dot { width: 10px; height: 10px; border-radius: 50%; background: var(--ink); flex: none; }
  .brand-mini__name { font-size: 8.5px; font-weight: 500; line-height: 1; white-space: nowrap; }

  /* Photo side */
  .photo { position: absolute; }
  .photo--cottage { left: 19px; top: 45px; width: 215px; height: 328px; background: linear-gradient(160deg, #9cb7cf 0%, #4c6b4a 35%, #2f4a3a 60%, #8a7a66 100%); }
  .photo--living { left: 241px; top: 45px; width: 215px; height: 162px; background: linear-gradient(180deg, #c99a55 0%, #8a5a2e 55%, #d8d2c4 80%, #5a3a1f 100%); }
  .photo--garden { left: 463px; top: 45px; width: 215px; height: 162px; background: linear-gradient(180deg, #6f9fd8 0%, #b7cde6 35%, #5c7d3e 65%, #8c6b4a 100%); }
  .photo--rainbow { left: 241px; top: 214px; width: 215px; height: 159px; background: linear-gradient(180deg, #5f6a80 0%, #7e8797 40%, #3d5a32 75%, #5d8a3c 100%); }
  .photo--sunset { left: 463px; top: 214px; width: 215px; height: 159px; background: linear-gradient(180deg, #3b3d4f 0%, #c7774a 40%, #2a1d18 65%, #0f0c0b 100%); }

  .tagline {
    position: absolute; left: 0; right: 0; top: 402px; text-align: center; white-space: nowrap;
  }
  .tagline__name { font-size: 28px; font-weight: 500; letter-spacing: -0.3px; }
  .tagline__line { font-size: 17px; font-weight: 300; letter-spacing: -0.3px; }
  .location {
    position: absolute; left: 0; right: 0; top: 462px; text-align: center;
    font-size: 19px; font-weight: 300; font-style: italic; letter-spacing: 0.3px;
  }
</style>
</head>
<body>

<section class="postcard postcard--mailing" aria-label="Postcard mailing side">
  <div class="brand-backdrop" aria-hidden="true">
    <div class="brand-backdrop__circle"></div>
    <div class="brand-backdrop__name">The Kingfisher's<br>Perch</div>
  </div>

  <h1 class="headline">Come see what all<br>of the buzz is about</h1>
  <div class="stamp-box" aria-label="Stamp area"></div>

  <div class="rule rule--greeting"></div>
  <div class="message-lines">
    <div class="rule" style="top:212px"></div>
    <div class="rule" style="top:235px"></div>
    <div class="rule" style="top:259px"></div>
    <div class="rule" style="top:282px"></div>
    <div class="rule" style="top:306px"></div>
    <div class="rule" style="top:329px"></div>
    <div class="rule" style="top:353px"></div>
    <div class="rule" style="top:376px"></div>
    <div class="rule" style="top:399px"></div>
    <div class="rule" style="top:423px"></div>
    <div class="rule" style="top:446px"></div>
  </div>
  <div class="address-lines">
    <div class="rule" style="top:393px"></div>
    <div class="rule" style="top:419px"></div>
    <div class="rule" style="top:446px"></div>
  </div>

  <p class="contact contact--listing">www.klwtstays.example/417294</p>
  <div class="brand-mini">
    <span class="brand-mini__dot"></span>
    <span class="brand-mini__name">The Kingfisher's Perch</span>
  </div>
  <p class="contact contact--social">www.chatterly.example/thefinestperchontheridge</p>
</section>

<section class="postcard postcard--photo" aria-label="Postcard photo side">
  <div class="photo photo--cottage" role="img" aria-label="Photo of the green two-storey cottage with porch and garden steps"></div>
  <div class="photo photo--living" role="img" aria-label="Photo of the warm-lit living room with sofa and kitchen"></div>
  <div class="photo photo--garden" role="img" aria-label="Photo of the garden path with flowers under a blue sky"></div>
  <div class="photo photo--rainbow" role="img" aria-label="Photo of a rainbow over the green lawn and trees"></div>
  <div class="photo photo--sunset" role="img" aria-label="Photo of a sunset over the valley with silhouetted trees"></div>

  <p class="tagline"><span class="tagline__name">The Kingfisher's Perch</span><span class="tagline__line"> - the finest perch on the ridge!</span></p>
  <p class="location">Cedarholm, WA USA</p>
</section>

</body>
</html>
```